Halvor Grading and Septic needs a flyer to submit to contractors to offer our services

I need a sleek profession one page full color high gloss document showcasing our services to give to Mobile Home Companies and contractors that need our services.

Target Market(s)

Home Builders. Mobile Home Salesmen. People Building new homes.

Industry/Entity Type

Construction

Font styles to use
Serif
Sans Serif

Requirements
Must have
• Phone Number. Email address. Logo. Services offered: Mobile Home Pads, Meter Pole Placement and Connection, Waterline Connection, On Site Septic System Installs
Should not have
• Jokes, Nothing trying to be cute

```html
<!DOCTYPE html>
<html lang="en">
<head>
<meta charset="utf-8">
<title>Halvor Grading and Septic – Septic Services Flyer</title>
<link rel="stylesheet" href="https://fonts.googleapis.com/css2?family=Open+Sans:wght@700;800&family=Roboto+Condensed:wght@500&display=swap">
<style>
  :root {
    --page-bg: #e6e6e6;
    --white: #ffffff;
    --navy: #1d4a7e;
    --navy-deep: #163a66;
    --red: #b3121a;
    --red-bright: #e4151d;
    --red-deep: #7e0c11;
    --ink: #1c1c1c;
  }
  html, body {
    margin: 0;
    padding: 0;
    width: 1200px;
    height: 3000px;
    overflow: hidden;
    background: var(--page-bg);
  }
  .flyer {
    position: absolute;
    left: 40px;
    top: 712px;
    width: 1120px;
    height: 1575px;
    display: block;
    box-shadow: 0 10px 30px rgba(0,0,0,0.18);
  }
  .brand-name { font-family: "Open Sans", sans-serif; font-weight: 800; fill: var(--navy); }
  .headline { font-family: "Open Sans", sans-serif; font-weight: 800; fill: var(--white); letter-spacing: 1px; }
  .section-title { font-family: "Open Sans", sans-serif; font-weight: 800; }
  .service-label { font-family: "Open Sans", sans-serif; font-weight: 700; fill: var(--ink); font-size: 11.5px; text-anchor: middle; }
  .contact-phone { font-family: "Open Sans", sans-serif; font-weight: 700; fill: var(--white); font-size: 25px; }
  .contact-line { font-family: "Roboto Condensed", sans-serif; font-weight: 500; fill: var(--white); font-size: 11.5px; }
  .icon-ring { fill: var(--white); stroke: var(--navy); stroke-width: 2.5; }
  .icon-ring-accent { fill: none; stroke: var(--red-bright); stroke-width: 3; }
  .icon-line { fill: none; stroke: var(--ink); stroke-width: 1.8; stroke-linecap: round; stroke-linejoin: round; }
  .call-icon { fill: var(--white); }
  .divider { stroke: #9fb3cc; stroke-width: 1; }
</style>
</head>
<body>
<svg class="flyer" viewBox="0 0 722 1015" xmlns="http://www.w3.org/2000/svg">
  <defs>
    <linearGradient id="navy-band" x1="0" y1="0" x2="1" y2="0">
      <stop offset="0" stop-color="#163a66"/>
      <stop offset="1" stop-color="#2a63a6"/>
    </linearGradient>
    <linearGradient id="red-band" x1="0" y1="0" x2="1" y2="1">
      <stop offset="0" stop-color="#8f0e14"/>
      <stop offset="0.5" stop-color="#b3121a"/>
      <stop offset="1" stop-color="#7e0c11"/>
    </linearGradient>
    <linearGradient id="tank-photo" x1="0" y1="0" x2="0" y2="1">
      <stop offset="0" stop-color="#2f63c8"/>
      <stop offset="0.55" stop-color="#8fb1e6"/>
      <stop offset="0.7" stop-color="#b08760"/>
      <stop offset="1" stop-color="#7b9a55"/>
    </linearGradient>
    <linearGradient id="dig-photo" x1="0" y1="0" x2="0" y2="1">
      <stop offset="0" stop-color="#5c7a3e"/>
      <stop offset="0.35" stop-color="#a88458"/>
      <stop offset="1" stop-color="#c49a6a"/>
    </linearGradient>
    <linearGradient id="yard-photo" x1="0" y1="0" x2="0" y2="1">
      <stop offset="0" stop-color="#6d8a4a"/>
      <stop offset="1" stop-color="#b89a78"/>
    </linearGradient>
  </defs>

  <rect class="sheet" x="0" y="0" width="722" height="1015" fill="var(--white)"/>

  <!-- header navy bands -->
  <polygon points="330,10 722,10 722,482 225,482" fill="url(#navy-band)"/>
  <polygon points="0,255 318,222 292,292 0,292" fill="url(#navy-band)"/>
  <polygon points="88,300 258,300 245,326 80,326" fill="var(--red)"/>

  <!-- hero photo -->
  <polygon role="img" aria-label="Photo: precast concrete septic tank lifted from a truck boom by a worker" points="352,40 722,40 722,482 232,482" fill="url(#tank-photo)"/>
  <rect role="img" aria-label="Photo: mobile home on a finished pad" x="270" y="385" width="142" height="78" fill="url(#yard-photo)" stroke="var(--white)" stroke-width="3"/>
  <rect role="img" aria-label="Photo: mobile home set on site" x="427" y="385" width="122" height="78" fill="#a9b3bd" stroke="var(--white)" stroke-width="3"/>
  <rect role="img" aria-label="Photo: green septic risers in a yard" x="568" y="385" width="122" height="78" fill="#7d7355" stroke="var(--white)" stroke-width="3"/>

  <!-- left photo under brand -->
  <polygon points="250,326 300,326 262,487 218,487" fill="var(--red)"/>
  <polygon role="img" aria-label="Photo: excavator beside an installed septic tank" points="0,326 250,326 218,487 0,487" fill="url(#dig-photo)"/>

  <!-- brand -->
  <rect x="36" y="68" width="14" height="14" fill="var(--red)"/>
  <text class="brand-name" x="60" y="82" font-size="27">HALVOR GRADING</text>
  <text class="brand-name" x="60" y="114" font-size="27">&amp; SEPTIC</text>
  <text class="brand-name" x="60" y="142" font-size="17" letter-spacing="2">555.201.0147</text>

  <!-- headline band -->
  <polygon points="22,490 722,490 722,606 0,606 0,572" fill="url(#red-band)"/>
  <text class="headline" x="370" y="572" font-size="57" text-anchor="middle">SEPTIC SERVICES</text>

  <!-- lower left photo -->
  <rect role="img" aria-label="Photo: excavator digging a septic trench beside a mobile home" x="0" y="612" width="285" height="334" fill="url(#dig-photo)"/>

  <!-- right lower red accent -->
  <polygon points="722,760 722,1015 530,1015" fill="url(#red-band)"/>

  <!-- service area -->
  <text class="section-title" x="324" y="663" font-size="31"><tspan fill="var(--red)">SERVICE</tspan> <tspan fill="var(--navy)">AREA</tspan></text>

  <line class="divider" x1="418" y1="690" x2="418" y2="770"/>
  <line class="divider" x1="553" y1="690" x2="553" y2="770"/>
  <line class="divider" x1="418" y1="800" x2="418" y2="890"/>

  <!-- pads -->
  <g class="service" transform="translate(360,727)">
    <circle class="icon-ring" r="30"/>
    <path class="icon-ring-accent" d="M -30 0 A 30 30 0 0 0 14 26.5"/>
    <path class="icon-line" d="M -11 -13 L 9 -13 L 13 -9 L 13 13 L -11 13 Z M -5 7 L -5 -2 M 0 7 L 0 -6 M 5 7 L 5 -3"/>
  </g>
  <text class="service-label" x="360" y="783">PADS</text>

  <!-- meter pole -->
  <g class="service" transform="translate(487,720)">
    <circle class="icon-ring" r="30"/>
    <path class="icon-ring-accent" d="M -30 0 A 30 30 0 0 0 14 26.5"/>
    <path class="icon-line" d="M -8 -16 L -8 16 M -16 -12 L 0 -12 M -14 -7 L -2 -7 M 2 0 L 16 0 L 16 12 L 2 12 Z M 6 6 L 12 6"/>
  </g>
  <text class="service-label" x="487" y="780">METER POLE</text>
  <text class="service-label" x="487" y="795">AND ELECTRIC</text>

  <!-- water lines -->
  <g class="service" transform="translate(610,715)">
    <circle class="icon-ring" r="30"/>
    <path class="icon-ring-accent" d="M -30 0 A 30 30 0 0 0 14 26.5"/>
    <path class="icon-line" d="M -12 -14 L -12 4 A 12 12 0 0 0 12 4 L 12 -14 M -4 -14 L -4 4 A 4 4 0 0 0 4 4 L 4 -14 M -15 -14 L -1 -14 M 1 -14 L 15 -14"/>
  </g>
  <text class="service-label" x="610" y="775">WATER</text>
  <text class="service-label" x="610" y="790">LINES</text>

  <!-- septic systems -->
  <g class="service" transform="translate(362,836)">
    <circle class="icon-ring" r="30"/>
    <path class="icon-ring-accent" d="M -30 0 A 30 30 0 0 0 14 26.5"/>
    <ellipse class="icon-line" cx="0" cy="-8" rx="14" ry="5"/>
    <path class="icon-line" d="M -14 -8 L -14 10 A 14 5 0 0 0 14 10 L 14 -8"/>
  </g>
  <text class="service-label" x="362" y="893">SEPTIC</text>
  <text class="service-label" x="362" y="908">SYSTEMS</text>

  <!-- design & evaluation -->
  <g class="service" transform="translate(487,833)">
    <circle class="icon-ring" r="30"/>
    <path class="icon-ring-accent" d="M -30 0 A 30 30 0 0 0 14 26.5"/>
    <path class="icon-line" d="M -12 -15 L 8 -15 L 8 -4 M -12 -15 L -12 14 L 0 14 M -7 -9 L 3 -9 M -7 -4 L -1 -4"/>
    <circle class="icon-line" cx="5" cy="5" r="7"/>
    <path class="icon-line" d="M 10 10 L 16 16"/>
  </g>
  <text class="service-label" x="487" y="893">SEPTIC DESIGN</text>
  <text class="service-label" x="487" y="908">AND SITE</text>
  <text class="service-label" x="487" y="923">EVALUATION</text>

  <!-- device with service map -->
  <g transform="rotate(-18 646 895)">
    <rect role="img" aria-label="Illustration: smartphone showing a map of the service region" x="600" y="815" width="92" height="160" rx="13" fill="#dfe4ea" stroke="#8c939b" stroke-width="3"/>
  </g>

  <!-- contact bar -->
  <polygon points="0,946 300,946 300,1015 0,1015" fill="var(--red-bright)"/>
  <polygon points="290,946 550,946 505,1015 290,1015" fill="var(--navy)"/>
  <path class="call-icon" transform="translate(22,969) scale(0.95)" d="M 4 2 L 8 2 L 10 7 L 7.5 9 Q 9 13 13 15 L 15 12.5 L 20 14.5 L 20 18.5 Q 20 21 17 21 Q 3 20 2 5 Q 2 2 4 2 Z"/>
  <text class="contact-phone" x="48" y="989">(555) 201-0147</text>

  <circle cx="322" cy="967" r="4.5" fill="none" stroke="var(--white)" stroke-width="1.2"/>
  <path d="M 317.5 967 L 326.5 967 M 322 962.5 Q 319 967 322 971.5 Q 325 967 322 962.5" fill="none" stroke="var(--white)" stroke-width="1"/>
  <text class="contact-line" x="333" y="971">www.halvorgradingandseptic.com</text>
  <rect x="317.5" y="985" width="9" height="7" fill="none" stroke="var(--white)" stroke-width="1.1"/>
  <path d="M 317.5 985 L 322 989 L 326.5 985" fill="none" stroke="var(--white)" stroke-width="1.1"/>
  <text class="contact-line" x="333" y="993">owen@halvorgradingandseptic.com</text>
</svg>
</body>
</html>
```